Website for a new t-shirt company called bolddawnapperal.com

We are looking for a talented web designer to create a website that aligns with our brand's message and identity centered around the theme of "Bold Dawn." The website should be modern, clean, and visually appealing while also being user-friendly and easy to navigate.

We will be using the Big Commerce platform for our online store section, so the designer should have experience in designing websites on this platform.

We would like the website to have the following elements:

A color scheme that aligns with the brand's identity and message
A homepage that showcases our products and message, with clear calls-to-action for visitors to explore further
A blog section that highlights our brand's philosophy and offers advice and tips for people looking to make positive changes in their lives
An "About Us" section that introduces our brand and team and offers insight into our mission and values
A contact form that allows visitors to easily get in touch with us for inquiries or support
We are open to creative suggestions and ideas from the designer, but we would like the website to have a modern and minimalist aesthetic that resonates with our target audience of 20 to 40-year-olds.

```html
<!DOCTYPE html>
<html lang="en">
<head>
<meta charset="utf-8">
<title>Bold Dawn</title>
<link href="https://fonts.googleapis.com/css2?family=Playfair+Display:wght@400;500&family=Arimo:wght@400;700&display=swap" rel="stylesheet">
<style>
:root{--orange:#ec6a14;--ink:#222;--muted:#666;--line:#333;--footer:#333;--card:#ddd;--grey:#8a8a8a}
*{margin:0;padding:0;box-sizing:border-box}
html,body{width:1200px;height:4018px;overflow:hidden;background:#fff}
body{position:relative;font-family:Arimo,Arial,sans-serif;color:var(--ink)}
.abs{position:absolute}
.serif{font-family:"Playfair Display",Georgia,serif}
.topbar{left:0;top:0;width:1200px;height:41px;background:var(--orange);color:#fff;font-size:14px;font-weight:700;text-align:center;line-height:41px}
.search{left:111px;top:78px;width:309px;height:28px;border-bottom:2px solid var(--line);font-size:13px;line-height:24px;padding-left:20px}
.search svg{position:absolute;left:0;top:6px}
.logo{left:0;width:1200px;top:62px;text-align:center;font-size:44px}
.account{right:111px;top:86px;font-size:14px;font-weight:700}
.nav{left:0;width:1200px;top:147px;text-align:center;font-size:14px;font-weight:700}
.nav span{margin:0 24px}
.nav .on{color:var(--orange);font-weight:400}
.hero-l{left:0;top:180px;width:600px;height:600px;background:linear-gradient(135deg,#c9b8a4,#9a9690 60%,#7b7670)}
.hero-r{left:600px;top:180px;width:600px;height:600px;background:linear-gradient(135deg,#7a4a28,#c58a50 50%,#e7e2dc)}
.arrow{top:463px;width:36px;height:36px;background:#fff;display:flex;align-items:center;justify-content:center}
.caption{left:300px;top:641px;width:600px;height:280px;background:#fff;text-align:center}
.caption h1{font-weight:500;font-size:46px;margin-top:38px}
.caption p{font-size:18px;line-height:26px;margin-top:10px;color:#333}
.btn{display:inline-block;border:2px solid var(--orange);font-size:14px;font-weight:700;text-align:center}
.dots{left:0;width:1200px;top:886px;text-align:center;font-size:0}
.dots i{display:inline-block;width:7px;height:7px;border-radius:50%;border:1px solid #333;margin:0 1px}
.about-img{left:111px;top:971px;width:601px;height:514px;background:linear-gradient(135deg,#c7c29a,#b9a180 50%,#6b6a48)}
.about-box{left:643px;top:1045px;width:445px;height:367px;background:var(--orange);color:#fff;text-align:center}
.about-box h2{font-size:40px;font-weight:500;margin-top:52px}
.about-box p{font-size:15px;line-height:27px;margin:14px 30px 0}
.about-box .btn{border-color:#fff;color:#fff;width:142px;height:46px;line-height:42px;margin-top:24px}
.title{left:0;width:1200px;text-align:center;font-size:48px;font-weight:500}
.rule{left:572px;width:56px;height:3px;background:var(--orange)}
.card{width:226px;height:256px;border:1px solid var(--card);background:#fff}
.shirt{position:absolute;left:38px;top:34px;width:150px;height:180px;border-radius:30px 30px 6px 6px}
.sale{position:absolute;left:0;top:0;background:var(--grey);color:#fff;font-size:10px;font-weight:700;padding:4px 12px}
.qv{position:absolute;top:217px;height:28px;font-size:8px;font-weight:700;line-height:26px;text-align:center}
.pname{font-size:18px;line-height:25px;width:200px}
.price{font-size:14px;color:#555}
.price s{margin-right:10px}
.pdesc{font-size:14px;color:#555}
.blog-img{top:2801px;width:306px;height:214px}
.date{font-size:14px;color:#555}
.btitle{font-size:18px}
.btext{font-size:14px;line-height:23px;color:#777;width:300px}
.more{font-size:13px;font-weight:700;color:var(--orange)}
.field{border-bottom:2px solid var(--line);font-size:14px;padding-bottom:6px}
.footer{left:0;top:3667px;width:1200px;height:351px;background:var(--footer);color:#fff}
.fh{font-size:16px;font-weight:700;top:70px}
.fl{font-size:12.5px;line-height:26px;top:96px}
.soc{top:100px;width:30px;height:30px;border-radius:50%;background:#fff}
.pay{top:3973px;width:48px;height:27px;background:#fff;border-radius:2px}
</style>
</head>
<body>
<div class="abs topbar">FREE SHIPPING FOR ALL ORDERS</div>
<div class="abs search"><svg width="12" height="12" viewBox="0 0 12 12"><circle cx="5" cy="5" r="3.8" fill="none" stroke="#222" stroke-width="2"/><line x1="8" y1="8" x2="11.5" y2="11.5" stroke="#222" stroke-width="2"/></svg>Search Products...</div>
<div class="abs logo serif">Bold Dawn</div>
<div class="abs account">&#9711; SIGN IN &nbsp;&nbsp;|&nbsp;&nbsp; &#9634; (0)</div>
<div class="abs nav"><span class="on">HOME</span><span>ABOUT US</span><span>FEATURED PRODUCTS</span><span>BEST SELLERS</span><span>BLOG</span><span>CONTACT US</span></div>

<div class="abs hero-l" role="img" aria-label="Smiling man in a grey sweatshirt on a city street"></div>
<div class="abs hero-r" role="img" aria-label="Woman in a white t-shirt inside a warm-lit cafe"></div>
<div class="abs arrow" style="left:34px"><svg width="12" height="14"><path d="M9 1 3 7l6 6" fill="none" stroke="#222" stroke-width="2.5"/></svg></div>
<div class="abs arrow" style="left:1130px"><svg width="12" height="14"><path d="M3 1l6 6-6 6" fill="none" stroke="#222" stroke-width="2.5"/></svg></div>
<div class="abs caption">
<h1 class="serif">Bold Dawn</h1>
<p>Lorem ipsum dolor sit amet, consectetur adipiscing elit,<br>sed do eiusmod tempor incididunt.</p>
<a class="btn" style="width:132px;height:43px;line-height:39px;margin-top:24px">BUY NOW</a>
</div>
<div class="abs dots"><i style="background:#333"></i><i></i></div>

<div class="abs about-img" role="img" aria-label="Older couple in white t-shirts smiling outdoors"></div>
<div class="abs about-box">
<h2 class="serif">About Us</h2>
<p>Lorem ipsum dolor sit amet, consectetur adipiscing elit, sed do eiusmod tempor incididunt ut labore et dolore magna aliqua. Ut enim ad minim veniam, quis nostrud exercitation ullamco laboea.</p>
<a class="btn">LEARN MORE</a>
</div>

<div class="abs title serif" style="top:1582px">Featured Products</div>
<div class="abs rule" style="top:1642px"></div>

<div class="abs card" style="left:111px;top:1692px"><div class="shirt" role="img" aria-label="Navy t-shirt" style="background:#2a3050"></div></div>
<div class="abs card" style="left:361px;top:1692px"><div class="shirt" role="img" aria-label="Black t-shirt" style="background:#151515"></div><span class="sale">SALE</span></div>
<div class="abs card" style="left:612px;top:1692px"><div class="shirt" role="img" aria-label="White polo shirt" style="background:#f1f1f1;height:165px"></div><span class="qv" style="left:19px;width:91px;border:1px solid var(--orange)">QUICK VIEW</span><span class="qv" style="left:116px;width:91px;background:var(--orange);color:#fff">ADD TO CART</span></div>
<div class="abs card" style="left:862px;top:1692px"><div class="shirt" role="img" aria-label="Orange t-shirt" style="background:#f57a1c"></div><span class="sale">SALE</span></div>

<div class="abs pname" style="left:111px;top:1962px">Lorem ipsum dolor sit amet consecea</div>
<div class="abs price" style="left:111px;top:2019px">$65.00</div>
<div class="abs pdesc" style="left:111px;top:2046px">Sed ut perspiciatis</div>
<div class="abs pname" style="left:361px;top:1962px">Lorem ipsum dolor sit amet consecea</div>
<div class="abs price" style="left:361px;top:2019px"><s>$85.00</s>$65.00</div>
<div class="abs pdesc" style="left:361px;top:2046px">Sed ut perspiciatis</div>
<div class="abs pname" style="left:612px;top:1962px">Lorem ipsum dolor sit amet consecea</div>
<div class="abs price" style="left:612px;top:2019px">$65.00</div>
<div class="abs pdesc" style="left:612px;top:2046px">Sed ut perspiciatis</div>
<div class="abs pname" style="left:862px;top:1962px">Lorem ipsum dolor sit amet consecea</div>
<div class="abs price" style="left:862px;top:2019px"><s>$85.00</s>$65.00</div>
<div class="abs pdesc" style="left:862px;top:2046px">Sed ut perspiciatis</div>

<div class="abs title serif" style="top:2140px">Best Sellers</div>
<div class="abs rule" style="top:2200px"></div>

<div class="abs card" style="left:111px;top:2249px"><div class="shirt" role="img" aria-label="Red t-shirt" style="background:#b5101c"></div></div>
<div class="abs card" style="left:361px;top:2249px"><div class="shirt" role="img" aria-label="Blue t-shirt" style="background:#2a78cf"></div></div>
<div class="abs card" style="left:612px;top:2249px"><div class="shirt" role="img" aria-label="Navy t-shirt" style="background:#2a3050;height:165px"></div><span class="qv" style="left:19px;width:91px;border:1px solid var(--orange)">QUICK VIEW</span><span class="qv" style="left:116px;width:91px;background:var(--orange);color:#fff">ADD TO CART</span></div>
<div class="abs card" style="left:862px;top:2249px"><div class="shirt" role="img" aria-label="Green t-shirt" style="background:#10580f"></div></div>

<div class="abs pname" style="left:111px;top:2519px">Lorem ipsum dolor sit amet consecea</div>
<div class="abs price" style="left:111px;top:2576px">$65.00</div>
<div class="abs pdesc" style="left:111px;top:2603px">Sed ut perspiciatis</div>
<div class="abs pname" style="left:361px;top:2519px">Lorem ipsum dolor sit amet consecea</div>
<div class="abs price" style="left:361px;top:2576px"><s>$85.00</s>$65.00</div>
<div class="abs pdesc" style="left:361px;top:2603px">Sed ut perspiciatis</div>
<div class="abs pname" style="left:612px;top:2519px">Lorem ipsum dolor sit amet consecea</div>
<div class="abs price" style="left:612px;top:2576px">$65.00</div>
<div class="abs pdesc" style="left:612px;top:2603px">Sed ut perspiciatis</div>
<div class="abs pname" style="left:862px;top:2519px">Lorem ipsum dolor sit amet consecea</div>
<div class="abs price" style="left:862px;top:2576px"><s>$85.00</s>$65.00</div>
<div class="abs pdesc" style="left:862px;top:2603px">Sed ut perspiciatis</div>

<div class="abs title serif" style="top:2688px">Recent Blog</div>
<div class="abs rule" style="top:2749px"></div>

<div class="abs blog-img" role="img" aria-label="Cheerful woman in a pink t-shirt on a pink backdrop" style="left:111px;background:linear-gradient(135deg,#e8a3b4,#d88aa0)"></div>
<div class="abs blog-img" role="img" aria-label="Couple in black t-shirts against a dark wall" style="left:447px;background:linear-gradient(135deg,#3a3a3a,#1c1c1c)"></div>
<div class="abs blog-img" role="img" aria-label="Man in sunglasses and a patterned shirt outdoors" style="left:782px;background:linear-gradient(135deg,#e6e4de,#8d6a50 55%,#2a2a2a)"></div>

<div class="abs" style="left:111px;top:3033px"><div class="date">2023 Aug 22</div><div class="btitle" style="margin-top:10px">Lorem ipsum dolor sit amet</div><p class="btext" style="margin-top:8px">Lorem ipsum dolor sit amet, consectetur adi piscing elit, sed do eiusmod tempor incididu ut labore et dolore magna.</p><div class="more" style="margin-top:8px">READ MORE &nbsp;&#187;</div></div>
<div class="abs" style="left:447px;top:3033px"><div class="date">2023 Aug 22</div><div class="btitle" style="margin-top:10px">Lorem ipsum dolor sit amet</div><p class="btext" style="margin-top:8px">Lorem ipsum dolor sit amet, consectetur adi piscing elit, sed do eiusmod tempor incididu ut labore et dolore magna.</p><div class="more" style="margin-top:8px">READ MORE &nbsp;&#187;</div></div>
<div class="abs" style="left:782px;top:3033px"><div class="date">2023 Aug 22</div><div class="btitle" style="margin-top:10px">Lorem ipsum dolor sit amet</div><p class="btext" style="margin-top:8px">Lorem ipsum dolor sit amet, consectetur adi piscing elit, sed do eiusmod tempor incididu ut labore et dolore magna.</p><div class="more" style="margin-top:8px">READ MORE &nbsp;&#187;</div></div>

<div class="abs title serif" style="top:3252px">Get In Touch</div>
<div class="abs field" style="left:236px;top:3352px;width:360px">First Name</div>
<div class="abs field" style="left:605px;top:3352px;width:360px">Last Name</div>
<div class="abs field" style="left:236px;top:3399px;width:360px">Email</div>
<div class="abs field" style="left:605px;top:3399px;width:360px">Phone</div>
<div class="abs field" style="left:236px;top:3446px;width:729px;height:74px">Comments</div>
<a class="abs btn" style="left:534px;top:3541px;width:133px;height:45px;line-height:41px">CONTACT US</a>

<div class="abs footer">
<div class="abs fh" style="left:111px">LOCATION</div>
<div class="abs fl" style="left:111px;line-height:21px;top:102px">465, Lorem ipsum dolor sit amet,<br>United States</div>
<div class="abs fl" style="left:111px;top:148px"><span style="display:inline-block;width:10px;height:10px;background:var(--orange);border-radius:2px;margin-right:6px"></span>+1 (555) 014 2290</div>
<div class="abs fh" style="left:364px">CATEGORIES</div>
<div class="abs fl" style="left:364px">By Category<br>By Occasion<br>By Collection<br>Vintage<br>Gift Ideas<br>Best Sellers<br>Sale</div>
<div class="abs fh" style="left:557px">INFORMATION</div>
<div class="abs fl" style="left:557px">Shipping &amp; Returns<br>Contact Us<br>Blog<br>Sitemap</div>
<div class="abs fh" style="left:768px">COMPANY</div>
<div class="abs fl" style="left:768px">About<br>Products<br>Collections<br>Contact Us</div>
<div class="abs fh" style="left:941px">FOLLOW US</div>
<div class="abs soc" style="left:943px;background:var(--orange)"></div>
<div class="abs soc" style="left:983px"></div>
<div class="abs soc" style="left:1019px"></div>
<div class="abs soc" style="left:1057px"></div>
<div class="abs fl" style="right:111px;top:263px"><span style="display:inline-block;width:9px;height:9px;background:var(--orange);margin-right:6px"></span>Gift Certificates</div>
<div class="abs" style="left:111px;top:297px;width:978px;height:1px;background:#555"></div>
<div class="abs fl" style="right:111px;top:305px">&copy; 2023 Bold Dawn &nbsp;|&nbsp; All Rights Reserved</div>
</div>
<div class="abs pay" style="left:111px"></div>
<div class="abs pay" style="left:164px"></div>
<div class="abs pay" style="left:217px"></div>
<div class="abs pay" style="left:270px"></div>
<div class="abs pay" style="left:323px"></div>
</body>
</html>
```